Strategy and Technology Consulting - Our Story and Values Page

Interior Page design – Our History and Our Values

Our homepage has been designed and we are looking for a design for one of the interior pages. This interior page tells the story of Our History and Our Values

Because the homepage has been designed, we would like this interior page to reflect the design of the homepage without being a mirror image of the homepage.

This site will be implemented in WordPress using the Elementor framework.

Font: Poppins medium and Poppins dark
Illustrations: Our homepage illustrations were designed by “Brelin 1974” on Quillmark. Compatible original or stock illustrations are welcome. Stock photography is also welcome. Brelin is also available through Brelin Tosamek on Ravolo

Uploaded Files
• Homepage design – this is the design we will use for our homepage. Contest entries should reflect this basic style but should be distinctly different from the homepage.
• Our History and Our Values – Wireframe – the basic layout of the page we are looking for.
• Our History and Our Values – Word document with the text supporting the wireframe.
• Color Palette – please use colors compatible with the palette attached.

Our Story - timeline
There is a timeline element in the wireframe. The wireframe displays this as a series of chevrons (arrows), but it does not need to be. Creativity in display of the timeline is appreciated.

Our Values
If you look at the Word document, you will see that there are a lot of words on the page. The winning design will present the information in a way that engages the user without overwhelming them with too much to read. For example, they may click on a value and see more information.

Target Market(s)

CIO's and Technology Executives

Number of Pages Required

1 page

Font styles to use
Sans Serif
Other font styles liked:
• Poppin

Requirements
Must have
• A timeline element, all of our values
Nice to have
• Clever timeline display

```html
<!DOCTYPE html>
<html lang="en">
<head>
<meta charset="utf-8">
<title>Veltrane – Our Story and Values</title>
<link href="https://fonts.googleapis.com/css2?family=Poppins:wght@400;500;600;700;800&display=swap" rel="stylesheet">
<style>
:root{
  --canvas:#f2f2f4;
  --page:#ffffff;
  --band:#eef2f7;
  --ink:#3d4a5e;
  --text:#4b5566;
  --muted:#8a9099;
  --yellow:#f0b81e;
  --slate:#46566f;
  --slate-dark:#3b4a60;
  --slate-light:#6b7f9b;
  --line:#e2e6ec;
  --illus-a:#dbe5f7;
  --illus-b:#8fa9dd;
}
*{margin:0;padding:0;box-sizing:border-box}
html,body{width:1200px;height:3114px;overflow:hidden}
body{background:var(--canvas);font-family:'Poppins',sans-serif;color:var(--text);position:relative}
.abs{position:absolute}
.page-card{left:35px;top:40px;width:1112px;height:3028px;background:var(--page);box-shadow:0 2px 14px rgba(0,0,0,.08)}
.brand{font-weight:500;color:var(--muted);font-size:44px;letter-spacing:-0.5px;line-height:1}
.main-nav{top:69px;left:538px;display:flex;gap:22px;align-items:center;font-size:12px;font-weight:600;color:var(--ink)}
.main-nav span::after{content:" ⌄";font-size:10px}
.main-nav .home::after{content:""}
.btn-contact{background:var(--yellow);color:#fff;font-weight:700;font-size:11px;border-radius:20px;display:flex;align-items:center;justify-content:center;text-transform:uppercase}
.section-band{left:35px;width:1112px;background:var(--band)}
.section-title{font-size:31px;font-weight:700;color:var(--ink);line-height:1}
.timeline-year{top:258px;font-size:16px;font-weight:700;color:var(--ink)}
.timeline-line{left:145px;top:295px;width:889px;border-top:2px dotted #9aa3b0}
.timeline-dot{top:288px;width:15px;height:15px;border-radius:50%;border:1.5px dashed #8a93a0;background:#fff;margin-left:-7px}
.story-card{top:331px;height:150px;border:2px solid var(--line);display:flex;flex-direction:column;justify-content:center;padding:0 22px;gap:7px;font-size:13px;line-height:18px;color:var(--text)}
.story-card li{list-style:none;display:flex;gap:10px;align-items:flex-start}
.story-card li svg{flex:none;margin-top:3px}
.story-card .dash{width:12px;text-align:center;flex:none}
.value-title{font-size:23px;font-weight:700;color:var(--ink);line-height:28px}
.value-text{font-size:13px;line-height:18.6px;color:var(--text);margin-top:6px}
.value-illustration{border-radius:50%;background:radial-gradient(circle at 45% 45%,var(--illus-a) 0%,#c4d3f0 55%,var(--illus-b) 100%)}
.newsletter{left:163px;top:2413px;width:856px;height:191px;background:var(--yellow);border-radius:96px}
.newsletter-title{left:238px;top:2470px;font-size:30px;font-weight:800;color:#fff}
.newsletter-sub{left:238px;top:2516px;font-size:14px;font-weight:600;color:#fff;line-height:18px}
.email-field{left:671px;top:2488px;width:297px;height:43px;background:#fff;border-radius:22px;display:flex;align-items:center;padding-left:22px;gap:10px;font-size:12px;color:#9aa3b0}
.email-send{position:absolute;right:4px;top:4px;width:35px;height:35px;border-radius:50%;background:#a8b2c0;display:flex;align-items:center;justify-content:center}
.footer-title{font-size:18px;font-weight:700;color:#fff;top:2746px}
.footer-links{top:2792px;list-style:none;font-size:12px;color:#e6eaf0;line-height:29px}
.footer-links li::before{content:"›";margin-right:7px}
.contact-list{left:868px;top:2788px;width:200px;font-size:12px;color:#e6eaf0;line-height:16px}
.contact-item{display:flex;gap:8px;margin-bottom:18px}
.social{top:2840px;width:40px;height:40px;border-radius:50%;background:rgba(255,255,255,.22)}
.copyright{left:35px;top:3015px;width:1112px;height:53px;background:var(--slate-dark);color:#fff;font-size:12px;font-weight:500;display:flex;align-items:center;justify-content:center}
.chat-button{left:1086px;top:2992px;width:44px;height:44px;border-radius:50%;background:var(--yellow);display:flex;align-items:center;justify-content:center}
</style>
</head>
<body>

<div class="abs page-card"></div>

<!-- Header -->
<header>
  <div class="abs brand" style="left:120px;top:58px">Veltrane</div>
  <nav class="abs main-nav">
    <span class="home"><svg width="14" height="13" viewBox="0 0 14 13"><path d="M7 1 1 6.5h2V12h3V8.5h2V12h3V6.5h2z" fill="#9aa3b0"/></svg></span>
    <span>ABOUT US</span><span>SERVICES</span><span>INSIGHTS</span><span>JOIN US</span>
  </nav>
  <a class="abs btn-contact" style="left:943px;top:59px;width:120px;height:36px">Contact us</a>
</header>

<!-- Our Story -->
<section class="our-story">
  <div class="abs section-band" style="top:121px;height:69px"></div>
  <h2 class="abs section-title" style="left:117px;top:140px">Our Story</h2>

  <div class="abs timeline-year" style="left:129px">2017</div>
  <div class="abs timeline-year" style="left:378px">2019</div>
  <div class="abs timeline-year" style="left:485px">2020</div>
  <div class="abs timeline-year" style="left:660px">2021</div>
  <div class="abs timeline-year" style="left:772px">2022</div>
  <div class="abs timeline-year" style="left:1002px">Onward</div>
  <div class="abs timeline-line"></div>
  <div class="abs timeline-dot" style="left:145px"></div>
  <div class="abs timeline-dot" style="left:395px"></div>
  <div class="abs timeline-dot" style="left:504px"></div>
  <div class="abs timeline-dot" style="left:678px"></div>
  <div class="abs timeline-dot" style="left:790px"></div>
  <div class="abs timeline-dot" style="left:1034px"></div>

  <ul class="abs story-card" style="left:116px;width:305px">
    <li><svg width="12" height="12" viewBox="0 0 12 12"><circle cx="6" cy="6" r="6" fill="#f0b81e"/><path d="M3.3 6.2 5.2 8 8.8 4.2" stroke="#fff" stroke-width="1.6" fill="none"/></svg>Growth Strategy Focus</li>
    <li><svg width="12" height="12" viewBox="0 0 12 12"><circle cx="6" cy="6" r="6" fill="#f0b81e"/><path d="M3.3 6.2 5.2 8 8.8 4.2" stroke="#fff" stroke-width="1.6" fill="none"/></svg>Consistent, Modest Growth</li>
    <li><svg width="12" height="12" viewBox="0 0 12 12"><circle cx="6" cy="6" r="6" fill="#f0b81e"/><path d="M3.3 6.2 5.2 8 8.8 4.2" stroke="#fff" stroke-width="1.6" fill="none"/></svg>Preliminary Focus on Technology</li>
    <li><svg width="12" height="12" viewBox="0 0 12 12"><circle cx="6" cy="6" r="6" fill="#f0b81e"/><path d="M3.3 6.2 5.2 8 8.8 4.2" stroke="#fff" stroke-width="1.6" fill="none"/></svg>Eureka! Implementing strategy is hard</li>
  </ul>
  <ul class="abs story-card" style="left:479px;width:224px">
    <li><svg width="12" height="12" viewBox="0 0 12 12"><circle cx="6" cy="6" r="6" fill="#f0b81e"/><path d="M3.3 6.2 5.2 8 8.8 4.2" stroke="#fff" stroke-width="1.6" fill="none"/></svg>Pandemic Pauses Growth</li>
    <li><svg width="12" height="12" viewBox="0 0 12 12"><circle cx="6" cy="6" r="6" fill="#f0b81e"/><path d="M3.3 6.2 5.2 8 8.8 4.2" stroke="#fff" stroke-width="1.6" fill="none"/></svg>Rethinking:</li>
    <li><span class="dash">-</span>the business model</li>
    <li><span class="dash">-</span>the delivery model</li>
  </ul>
  <ul class="abs story-card" style="left:760px;width:306px">
    <li><svg width="12" height="12" viewBox="0 0 12 12"><circle cx="6" cy="6" r="6" fill="#f0b81e"/><path d="M3.3 6.2 5.2 8 8.8 4.2" stroke="#fff" stroke-width="1.6" fill="none"/></svg>Leadership Team for Focus on<br>Essential Areas</li>
    <li><svg width="12" height="12" viewBox="0 0 12 12"><circle cx="6" cy="6" r="6" fill="#f0b81e"/><path d="M3.3 6.2 5.2 8 8.8 4.2" stroke="#fff" stroke-width="1.6" fill="none"/></svg>Rapid Growth</li>
    <li><svg width="12" height="12" viewBox="0 0 12 12"><circle cx="6" cy="6" r="6" fill="#f0b81e"/><path d="M3.3 6.2 5.2 8 8.8 4.2" stroke="#fff" stroke-width="1.6" fill="none"/></svg>Customer Success</li>
  </ul>
</section>

<!-- Our Values -->
<section class="our-values">
  <div class="abs section-band" style="top:581px;height:68px"></div>
  <h2 class="abs section-title" style="left:117px;top:599px">Our Values</h2>

  <div class="abs value-illustration" role="img" aria-label="Illustration of people celebrating in front of a globe" style="left:278px;top:719px;width:181px;height:181px"></div>
  <div class="abs value-block" style="left:503px;top:734px;width:400px">
    <h3 class="value-title">The Value of Every Human.<br>Regardless.</h3>
    <p class="value-text">Each person's unique experiences and perspectives add vibrant hues to the tapestry of our shared existence. In a world where diversity paints the canvas of humanity, true beauty is found in recognizing the inherent and incalculable value of every human being.</p>
  </div>

  <div class="abs value-block" style="left:282px;top:985px;width:400px">
    <h3 class="value-title">Collaboration</h3>
    <p class="value-text">Collaboration in work transforms individual endeavors into symphonies of collective achievement. Through collaboration, diverse talents converge, fostering a rich exchange of ideas that amplifies creativity, accelerates progress, and brings forth solutions beyond what a single mind could conceive.</p>
  </div>
  <div class="abs value-illustration" role="img" aria-label="Illustration of two people fitting puzzle pieces above a light bulb" style="left:723px;top:961px;width:177px;height:175px"></div>

  <div class="abs value-illustration" role="img" aria-label="Illustration of a team launching a rocket" style="left:282px;top:1190px;width:189px;height:178px"></div>
  <div class="abs value-block" style="left:516px;top:1217px;width:390px">
    <h3 class="value-title">Passion</h3>
    <p class="value-text">Passion infuses our work with energy, transforming routine tasks into opportunities for creativity and innovation. Fueled by passion, individuals become unstoppable forces, driven to overcome challenges and achieve remarkable outcomes that benefit them and inspire those around them</p>
  </div>

  <div class="abs value-block" style="left:282px;top:1448px;width:400px">
    <h3 class="value-title">Excellence</h3>
    <p class="value-text">Excellence isn't a destination; it's a continuous journey of refinement and growth. Striving for excellence cultivates a culture of continuous improvement, fostering innovation, credibility, and a lasting impact that resonates far beyond the immediate task.</p>
  </div>
  <div class="abs value-illustration" role="img" aria-label="Illustration of people climbing steps toward a flag" style="left:723px;top:1438px;width:177px;height:157px"></div>

  <div class="abs value-illustration" role="img" aria-label="Illustration of people at a monitor with a target and charts" style="left:284px;top:1658px;width:169px;height:173px"></div>
  <div class="abs value-block" style="left:502px;top:1680px;width:390px">
    <h3 class="value-title">Tenacity</h3>
    <p class="value-text">Tenacity is the unwavering anchor that keeps us grounded amidst adversity, propelling us forward when faced with obstacles. The resilience to persist, adapt, and learn from setbacks leads to the mastery of skills and the fulfillment of ambitious goals.</p>
  </div>

  <div class="abs value-block" style="left:282px;top:1911px;width:405px">
    <h3 class="value-title">Solution Mindset</h3>
    <p class="value-text">A solution mindset is the compass that directs our focus from problems to possibilities. It empowers us to navigate challenges with a proactive mindset, igniting a journey of exploration and innovation that not only resolves issues but also paves the way for continuous growth and success.</p>
  </div>
  <div class="abs value-illustration" role="img" aria-label="Illustration of a person beside a brain with a light bulb" style="left:723px;top:1885px;width:177px;height:175px"></div>

  <div class="abs value-illustration" role="img" aria-label="Illustration of people around a large phone with gears and message icons" style="left:282px;top:2115px;width:181px;height:177px"></div>
  <div class="abs value-block" style="left:504px;top:2142px;width:400px">
    <h3 class="value-title">Generosity</h3>
    <p class="value-text">Generosity creates a virtuous cycle of goodwill, fostering a sense of unity and shared purpose among colleagues. By freely sharing knowledge, support, and resources, we uplift those around us and contribute to a collaborative environment where collective achievements flourish.</p>
  </div>
</section>

<!-- Footer -->
<footer>
  <svg class="abs" style="left:35px;top:2400px" width="1112" height="615" viewBox="0 0 1112 615" aria-hidden="true">
    <defs>
      <linearGradient id="footerFill" x1="0" y1="1" x2="1" y2="0">
        <stop offset="0" stop-color="#6b7f9b"/>
        <stop offset="0.5" stop-color="#4f607a"/>
        <stop offset="1" stop-color="#46566f"/>
      </linearGradient>
    </defs>
    <path d="M0 20 C160 40 280 230 480 248 C690 268 900 170 1112 120 L1112 615 L0 615 Z" fill="#d9dde3"/>
    <path d="M0 35 C160 60 280 262 480 282 C690 300 900 190 1112 145 L1112 615 L0 615 Z" fill="url(#footerFill)"/>
  </svg>

  <div class="abs newsletter"></div>
  <h2 class="abs newsletter-title">Subscribe Our Newsletter</h2>
  <p class="abs newsletter-sub">Subscribe our newsletter to receive the latest news<br>and exclusive offers every week, No spam.</p>
  <div class="abs email-field">
    <svg width="13" height="10" viewBox="0 0 13 10"><rect width="13" height="10" rx="1" fill="#9aa3b0"/><path d="M0.5 1 6.5 5.5 12.5 1" stroke="#fff" fill="none"/></svg>
    Enter email address
    <span class="email-send"><svg width="14" height="14" viewBox="0 0 14 14"><path d="M13 1 1 6l4.5 1.5L7 13z" fill="#fff"/></svg></span>
  </div>

  <div class="abs brand" style="left:150px;top:2780px;font-size:58px;color:#e3e7ee">Veltrane</div>
  <span class="abs social" style="left:198px" aria-label="Social link"></span>
  <span class="abs social" style="left:245px" aria-label="Social link"></span>
  <span class="abs social" style="left:292px" aria-label="Social link"></span>
  <span class="abs social" style="left:339px" aria-label="Social link"></span>
  <a class="abs btn-contact" style="left:234px;top:2902px;width:121px;height:35px">Contact us</a>

  <h4 class="abs footer-title" style="left:491px">Quick links</h4>
  <ul class="abs footer-links" style="left:491px">
    <li>Home</li><li>About Us</li><li>Services</li><li>Insights</li><li>Join Us</li><li>Contact Us</li>
  </ul>

  <h4 class="abs footer-title" style="left:654px">Our Services</h4>
  <ul class="abs footer-links" style="left:654px">
    <li>Business Transformation</li><li>ERP Implementations</li><li>ERP Solutions</li><li>BI and Data</li><li>Building the Right Team...</li>
  </ul>

  <h4 class="abs footer-title" style="left:868px">Contact info</h4>
  <div class="abs contact-list">
    <div class="contact-item"><svg width="12" height="10" viewBox="0 0 12 10"><rect width="12" height="10" rx="1" fill="#f0b81e"/><path d="M0.5 1 6 5 11.5 1" stroke="#46566f" fill="none"/></svg><span>Email:<br>hello@veltranegroup.com</span></div>
    <div class="contact-item"><svg width="12" height="12" viewBox="0 0 12 12"><path d="M2 1h3l1 3-1.5 1a7 7 0 0 0 2.5 2.5L8 6l3 1v3c0 1-1 1-1 1A9 9 0 0 1 1 2s0-1 1-1z" fill="#f0b81e"/></svg><span>Phone:<br>+44 100 555 0192</span></div>
    <div class="contact-item"><svg width="10" height="13" viewBox="0 0 10 13"><path d="M5 0a5 5 0 0 0-5 5c0 3.5 5 8 5 8s5-4.5 5-8a5 5 0 0 0-5-5z" fill="#f0b81e"/><circle cx="5" cy="5" r="2" fill="#46566f"/></svg><span>Location:<br>Some address line goes<br>here city name</span></div>
  </div>

  <div class="abs copyright">© Veltrane Design 2023, All Rights Reserved</div>
  <div class="abs chat-button" aria-label="Open chat">
    <svg width="22" height="20" viewBox="0 0 22 20"><path d="M11 1C5.5 1 1 4.6 1 9c0 2.3 1.2 4.3 3.1 5.8L3 19l4.6-2.4c1 .3 2.2.4 3.4.4 5.5 0 10-3.6 10-8S16.5 1 11 1z" fill="#fff"/><circle cx="7" cy="9" r="1.3" fill="#f0b81e"/><circle cx="11" cy="9" r="1.3" fill="#f0b81e"/><circle cx="15" cy="9" r="1.3" fill="#f0b81e"/></svg>
  </div>
</footer>

</body>
</html>
```